Business Card Design Project

Business Card
We are rebranding with a new logo
Industry/Entity Type
Business
Contact Information for Business Card
Dennis Morvale +61 487215963 dennis@quorv.com.au P.O. Box 872 Fernlow QLD 4309
Requirements
Must have
- Logo

```html
<!DOCTYPE html>
<html lang="en">
<head>
<meta charset="utf-8">
<title>Quorv International – Business Card</title>
<link href="https://fonts.googleapis.com/css2?family=Roboto:wght@400;500&family=Roboto+Condensed:wght@700&display=swap" rel="stylesheet">
<style>
  :root {
    --backdrop: #2a2a2a;
    --card-white: #f4f4f4;
    --brand-blue: #0a8fc8;
    --deep-blue: #05506f;
    --orange: #f7901e;
    --burnt-orange: #e5622a;
    --text-grey: #4a4a4a;
  }
  html, body {
    margin: 0;
    padding: 0;
    width: 1200px;
    height: 960px;
    overflow: hidden;
    background: var(--backdrop);
  }
  .card {
    position: absolute;
    left: 314px;
    top: 294px;
    width: 600px;
    height: 343px;
    border-radius: 16px;
    overflow: hidden;
    background: var(--card-white);
    font-family: "Roboto", Arial, sans-serif;
  }
  .card-band {
    position: absolute;
    left: 0;
    right: 0;
    bottom: 0;
    height: 72px;
    background: linear-gradient(90deg, var(--orange) 0%, var(--burnt-orange) 30%, var(--brand-blue) 62%, var(--deep-blue) 100%);
  }
  .holder-name {
    position: absolute;
    left: 31px;
    top: 30px;
    margin: 0;
    font-family: "Roboto Condensed", "Arial Narrow", sans-serif;
    font-weight: 700;
    font-size: 21px;
    color: var(--brand-blue);
    letter-spacing: 0.2px;
  }
  .postal-address {
    position: absolute;
    left: 31px;
    top: 139px;
    margin: 0;
    font-style: normal;
    font-size: 14px;
    line-height: 19px;
    color: var(--text-grey);
  }
  .contact-list {
    position: absolute;
    left: 31px;
    top: 182px;
    margin: 0;
    padding: 0;
    list-style: none;
    font-size: 14px;
    line-height: 19px;
    color: var(--text-grey);
  }
  .contact-list li {
    display: flex;
    align-items: center;
    gap: 9px;
  }
  .contact-icon {
    width: 13px;
    height: 13px;
    fill: var(--brand-blue);
    flex: none;
  }
  .brand-name {
    position: absolute;
    left: 282px;
    top: 60px;
    width: 200px;
    margin: 0;
    text-align: center;
    font-family: "Roboto Condensed", "Arial Narrow", sans-serif;
    font-weight: 700;
    color: var(--brand-blue);
    line-height: 1;
  }
  .brand-name .brand-word {
    display: block;
    font-size: 54px;
  }
  .brand-name .brand-tag {
    display: block;
    margin-top: 18px;
    font-size: 17px;
    letter-spacing: 3.3px;
  }
</style>
</head>
<body>
  <section class="card">
    <div class="card-band" role="img" aria-label="Decorative blue and orange background artwork"></div>

    <h1 class="holder-name">DENNIS MORVALE</h1>

    <p class="brand-name"><span class="brand-word">Quorv</span><span class="brand-tag">INTERNATIONAL</span></p>

    <address class="postal-address">P.O. Box 872<br>Fernlow QLD 4309</address>

    <ul class="contact-list">
      <li>
        <svg class="contact-icon" viewBox="0 0 24 24" aria-hidden="true"><path d="M6.6 10.8a15 15 0 0 0 6.6 6.6l2.2-2.2c.3-.3.7-.4 1-.2 1.1.4 2.3.6 3.6.6.6 0 1 .4 1 1V20c0 .6-.4 1-1 1A17 17 0 0 1 3 4c0-.6.4-1 1-1h3.5c.6 0 1 .4 1 1 0 1.3.2 2.5.6 3.6.1.3 0 .7-.2 1z"/></svg>
        <span>+61 487215963</span>
      </li>
      <li>
        <svg class="contact-icon" viewBox="0 0 24 24" aria-hidden="true"><path d="M2 5h20v14H2z M2 5l10 8 10-8" stroke="#f4f4f4" stroke-width="1.5"/></svg>
        <span>dennis@quorv.com.au</span>
      </li>
      <li>
        <svg class="contact-icon" viewBox="0 0 24 24" aria-hidden="true"><circle cx="12" cy="12" r="10"/><path d="M2 12h20M12 2c3 3 3 17 0 20M12 2c-3 3-3 17 0 20" stroke="#f4f4f4" stroke-width="1.4" fill="none"/></svg>
        <span>www.quorv.com.au</span>
      </li>
    </ul>
  </section>
</body>
</html>
```